Telvora website

Hello. Pray all is well. Peace be with you.

looking to make a website with pages information from https://veradilo.us. English and Spanish.

the header of quarnetel.com when in mobile version

clean vector images and layout of fendlecell.com

and the clean simple black and white look of tavesport.com

please use the attached logo for color guidance

also need the my account section for users to be designed

there should also be a countdown timer for days:hours:seconds on the home page

please do website in figma

```html
<!DOCTYPE html>
<html lang="en">
<head>
<meta charset="utf-8">
<title>Telvora — Connect to the Future</title>
<link href="https://fonts.googleapis.com/css2?family=Rubik:wght@300;400;700;800;900&family=Roboto:ital,wght@0,400;0,500;0,700;1,400&display=swap" rel="stylesheet">
<style>
:root{
  --green:#5b9672;
  --green-light:#7fb392;
  --ink:#111111;
  --black:#0c0c0c;
  --grey-bg:#f2f2f2;
  --text:#222222;
  --muted:#777777;
  --white:#ffffff;
  --line:#d9d9d9;
}
*{box-sizing:border-box;margin:0;padding:0}
html,body{width:1200px;height:4135px;overflow:hidden}
body{position:relative;font-family:"Roboto",Arial,sans-serif;color:var(--text);background:var(--white)}
.abs{position:absolute}
.heading{font-family:"Rubik",Arial,sans-serif;font-weight:300;color:var(--ink);text-align:center;font-size:46px;letter-spacing:.5px}
.heading b{font-weight:900}
.heading-rule{width:56px;height:3px;background:var(--green);margin:10px auto 0}
.btn{position:absolute;display:flex;align-items:center;justify-content:center;font:700 15px "Roboto",sans-serif;letter-spacing:.5px;text-transform:uppercase;color:var(--white);text-decoration:none}

/* hero */
.hero{left:0;top:0;width:1200px;height:648px;background:linear-gradient(115deg,#1a1a1a 0%,#0a0a0a 55%,#151515 100%)}
.nav a{position:absolute;top:57px;color:var(--white);font-size:13px;text-decoration:none}
.brand{position:absolute;left:0;width:1200px;top:22px;text-align:center;color:var(--white)}
.brand .mark{display:block;width:56px;height:56px;margin:0 auto 6px;border:3px solid var(--white)}
.brand .name{font:700 22px "Rubik",sans-serif}
.hero h1{position:absolute;left:111px;top:188px;font:300 47px/1.1 "Rubik",sans-serif;color:var(--white)}
.hero h1 b{font-weight:900}
.hero .lead{position:absolute;left:111px;top:362px;width:520px;font:500 16px/1.65 "Roboto",sans-serif;color:var(--white)}
.offer{left:0;width:1200px;top:561px;text-align:center;color:var(--white);font:500 16px "Roboto",sans-serif}
.countdown{left:367px;top:600px;width:464px;height:95px;background:var(--green);border-radius:6px;display:flex;align-items:center;justify-content:center;gap:10px}
.cd-box{width:68px;height:76px;border:2px solid var(--green-light);border-radius:4px;text-align:center;color:var(--white);background:#669f7c}
.cd-box .num{font:800 36px/1 "Rubik",sans-serif;padding-top:8px}
.cd-box .lbl{font-size:13px;margin-top:4px}
.cd-sep{color:var(--white);font:800 32px "Rubik",sans-serif;width:12px;text-align:center}
.hero-frame{left:730px;top:165px;width:359px;height:360px;border:22px solid var(--white)}
.hero-art{left:777px;top:112px;width:264px;height:542px;border-radius:38px;background:linear-gradient(180deg,#1d1d1d 0%,#1a2a21 55%,#8ccaa2 100%);border:4px solid #3b3b3b}

/* features */
.feature{position:absolute;top:874px;width:230px;text-align:center}
.feature .icon{width:77px;height:77px;margin:0 auto;border:3px solid var(--green);display:flex;align-items:center;justify-content:center}
.feature h3{margin-top:21px;font:700 16px "Roboto",sans-serif;color:var(--ink)}
.feature p{margin-top:8px;font-size:13.5px;line-height:1.4;color:var(--muted)}

/* checker */
.checker-bg{left:0;top:1123px;width:1200px;height:654px;background:var(--grey-bg)}
.card{position:absolute;top:1318px;width:467px;height:382px;background:var(--white);box-shadow:0 2px 10px rgba(0,0,0,.05)}
.card-tag{position:absolute;top:1288px;width:392px;height:61px;background:var(--black);color:var(--white);display:flex;align-items:center;justify-content:center;font:300 35px "Rubik",sans-serif}
.card-tag b{font-weight:900;margin-right:10px}
.card .prompt{position:absolute;top:68px;width:100%;text-align:center;font-size:16px;color:var(--ink)}
.zip{position:absolute;top:113px;left:62px;width:342px;height:38px;border:1px solid var(--line);background:#f7f7f7}
.zip span{position:absolute;left:10px;top:11px;font-size:13px;color:#999}
.zip .go{position:absolute;right:0;top:0;width:98px;height:36px;background:var(--green);color:var(--white);font:500 14px "Roboto",sans-serif;display:flex;align-items:center;justify-content:center}
.card .art{position:absolute;top:190px;left:100px;width:270px;height:176px}

/* activation */
.step{position:absolute;top:1960px;width:235px;height:178px;color:var(--white);text-align:center}
.step.dark{background:var(--black)}
.step.green{background:var(--green)}
.step .n{position:absolute;right:14px;top:4px;font:900 46px "Rubik",sans-serif;color:rgba(255,255,255,.35)}
.step svg{position:absolute;left:50%;top:30px;margin-left:-30px}
.step p{position:absolute;top:118px;width:100%;font:500 16px/1.3 "Roboto",sans-serif}

/* bring phone */
.byop{left:0;top:2238px;width:1200px;height:420px;background:radial-gradient(circle at 250px 210px,#ffffff 0%,#ececec 45%,#f3f3f3 100%);overflow:hidden}
.byop-art{position:absolute;left:125px;top:-10px;width:250px;height:440px;border-radius:36px;border:6px solid #bdbdbd;background:linear-gradient(135deg,#fafafa 0%,#e2e2e2 60%,#c4c4c4 100%);transform:rotate(-52deg)}
.byop h2{position:absolute;left:555px;top:55px;font:300 45px/1.14 "Rubik",sans-serif;color:var(--ink)}
.byop h2 b{font-weight:900}
.byop h2 .dash{display:inline-block;width:58px;height:3px;background:var(--green);vertical-align:middle;margin-left:20px}

/* testimonials */
.review{position:absolute;top:2844px;width:303px;height:199px;background:var(--white);border:1px solid #e3e3e3;box-shadow:7px 7px 0 var(--black)}
.review p{position:absolute;left:33px;top:30px;width:245px;font:italic 14px/1.65 "Roboto",sans-serif;color:#888}
.review .avatar{position:absolute;left:25px;top:146px;width:32px;height:32px;border-radius:50%;background:linear-gradient(#c9a88f,#6d4a38)}
.review .who{position:absolute;left:68px;top:143px;font:500 14px "Roboto",sans-serif;color:var(--ink)}
.review .stars{position:absolute;left:68px;top:163px;color:#f0b323;font-size:12px;letter-spacing:1px}
.review .quote{position:absolute;right:30px;top:118px;font:900 90px/1 "Rubik",sans-serif;color:#e6e6e6}

/* faq */
.faq-bg{left:0;top:3133px;width:1200px;height:637px;background:var(--grey-bg)}
.faq{position:absolute;left:220px;width:758px;background:var(--white);border-radius:26px;box-shadow:0 3px 6px rgba(0,0,0,.08)}
.faq .q{position:absolute;left:24px;top:18px;font:500 15px "Roboto",sans-serif;color:var(--ink)}
.faq .a{position:absolute;left:27px;top:50px;font-size:13px;color:#999}
.faq .chev{position:absolute;right:20px;top:16px;width:21px;height:21px;border-radius:50%;background:var(--green)}

/* footer */
.footer{left:0;top:3770px;width:1200px;height:365px;background:var(--black);color:var(--white)}
.foot-brand{left:114px;top:3838px;width:257px;text-align:center}
.foot-brand .mark{width:100px;height:100px;border:5px solid var(--white);margin:0 auto 12px}
.foot-brand .name{font:700 40px "Rubik",sans-serif;color:var(--white)}
.foot h4{position:absolute;font:700 18px "Roboto",sans-serif;color:var(--white)}
.foot-links{position:absolute;left:472px;top:3872px;list-style:none;font-size:14px;line-height:26.5px;color:var(--white)}
.email{left:717px;top:3875px;width:236px;height:44px;background:var(--white)}
.email span{position:absolute;left:22px;top:15px;font-size:11px;color:#999}
.social{position:absolute;top:3986px;width:30px;height:30px;border:2px solid var(--white);border-radius:50%}
.copy{left:0;width:1200px;top:4080px;text-align:center;font-size:13px;color:var(--white)}
</style>
</head>
<body>

<!-- Hero -->
<header class="hero abs">
  <nav class="nav">
    <a style="left:111px">Home</a>
    <a style="left:172px">Plans</a>
    <a style="left:230px">Bring Your Own phone</a>
    <a style="left:390px">Activate</a>
    <a style="left:742px">Coverage</a>
    <a style="left:824px">SupportAccount</a>
    <a style="left:948px">&#9675; Account</a>
    <a style="left:1038px">&#9679; En &#8964;</a>
  </nav>
  <div class="brand"><span class="mark"></span><span class="name">telvora</span></div>
  <h1>Connect to the Future<br>with <b>Telvora's 5G<br>Networks!</b></h1>
  <p class="lead">Discover our ultra-fast data plans and stylish phones that will elevate your digital experience.</p>
  <a class="btn" style="left:111px;top:444px;width:175px;height:48px;background:var(--green)">Shop Plans</a>
  <a class="btn" style="left:300px;top:444px;width:201px;height:48px;border:2px solid var(--white)">Bring Your Phone</a>
</header>
<div class="hero-frame abs"></div>
<div class="hero-art abs" role="img" aria-label="Smartphone showing the brand name above a green fox illustration"></div>
<div class="offer abs">Limited Time Offer Ends</div>
<div class="countdown abs">
  <div class="cd-box"><div class="num">03</div><div class="lbl">Day</div></div><div class="cd-sep">:</div>
  <div class="cd-box"><div class="num">12</div><div class="lbl">Hours</div></div><div class="cd-sep">:</div>
  <div class="cd-box"><div class="num">45</div><div class="lbl">Mins</div></div><div class="cd-sep">:</div>
  <div class="cd-box"><div class="num">30</div><div class="lbl">Secs</div></div>
</div>

<!-- Features -->
<div class="abs" style="left:0;width:1200px;top:758px"><h2 class="heading"><b>Our</b> Features</h2><div class="heading-rule"></div></div>
<div class="feature" style="left:108px"><div class="icon"><svg width="44" height="44" viewBox="0 0 44 44" fill="none" stroke="#222" stroke-width="2"><path d="M8 14l14-7 14 7v16l-14 7-14-7z"/><path d="M8 14l14 7 14-7M22 21v16"/></svg></div><h3>Free 2-Day Shipping</h3><p>Get your devices delivered swiftly at no extra cost.</p></div>
<div class="feature" style="left:358px"><div class="icon"><svg width="44" height="44" viewBox="0 0 44 44" fill="none" stroke="#222" stroke-width="2"><rect x="8" y="12" width="28" height="20" rx="2"/><path d="M8 18h28M13 27h8"/></svg></div><h3>No Credit Checks</h3><p>Stress-free sign-ups without the hassle.</p></div>
<div class="feature" style="left:610px"><div class="icon"><svg width="44" height="44" viewBox="0 0 44 44" fill="none" stroke="#222" stroke-width="2"><path d="M8 30a14 14 0 0128 0"/><path d="M22 30l7-9"/><circle cx="22" cy="30" r="2"/></svg></div><h3>5G Speed</h3><p>Experience ultra-fast connectivity like never before.</p></div>
<div class="feature" style="left:860px"><div class="icon"><svg width="44" height="44" viewBox="0 0 44 44" fill="none" stroke="#222" stroke-width="2"><path d="M11 6h16l6 6v26H11z"/><path d="M15 16h12M15 21h12M15 26h8"/><circle cx="31" cy="33" r="6"/><path d="M28 30l6 6M34 30l-6 6"/></svg></div><h3>No Annual Contracts</h3><p>Enjoy flexibility with zero long-term commitments.</p></div>

<!-- Coverage & Device Checker -->
<div class="checker-bg abs"></div>
<div class="abs" style="left:0;width:1200px;top:1177px"><h2 class="heading"><b>Coverage &amp; Device</b> Checker</h2><div class="heading-rule"></div></div>
<div class="card" style="left:111px">
  <p class="prompt">Enter your ZIP Code to get started</p>
  <div class="zip"><span>ZIP Code</span><div class="go">Let's Go</div></div>
  <div class="art" role="img" aria-label="Map of the United States with state outlines" style="background:radial-gradient(ellipse at center,#e4e4e4 0%,#f4f4f4 70%,#ffffff 100%)"></div>
</div>
<div class="card-tag" style="left:149px"><b>Coverage</b> Checker</div>
<div class="card" style="left:622px">
  <p class="prompt">Enter your ZIP Code to get started</p>
  <div class="zip"><span>ZIP Code</span><div class="go">Let's Go</div></div>
  <div class="art" role="img" aria-label="Landscape phone showing a stretching green fox illustration" style="left:62px;width:355px;height:172px;border:5px solid #222;border-radius:20px;background:linear-gradient(180deg,#ffffff 0%,#e7f2eb 60%,#5b9672 100%)"></div>
</div>
<div class="card-tag" style="left:659px"><b>Device</b> Checker</div>

<!-- Activation -->
<div class="abs" style="left:0;width:1200px;top:1854px"><h2 class="heading"><b>Activation</b> Process</h2><div class="heading-rule"></div></div>
<div class="step dark" style="left:111px"><span class="n">1</span>
  <svg width="60" height="64" viewBox="0 0 60 64" fill="none" stroke="#fff" stroke-width="2.5"><path d="M30 52S14 34 14 24a16 16 0 0132 0c0 10-16 28-16 28z"/><circle cx="30" cy="24" r="6"/><ellipse cx="30" cy="56" rx="16" ry="4"/></svg>
  <p>Check Coverage<br>in Your Area</p></div>
<div class="step green" style="left:359px"><span class="n">2</span>
  <svg width="60" height="64" viewBox="0 0 60 64" fill="none" stroke="#fff" stroke-width="2.5"><rect x="18" y="4" width="24" height="54" rx="4"/><path d="M27 10h6M26 52h8"/></svg>
  <p>Bring Your Phone or<br>Get a New One</p></div>
<div class="step dark" style="left:606px"><span class="n">3</span>
  <svg width="60" height="64" viewBox="0 0 60 64" fill="none" stroke="#fff" stroke-width="2.5"><rect x="12" y="8" width="36" height="52" rx="3"/><rect x="22" y="4" width="16" height="8" rx="2"/><rect x="18" y="20" width="6" height="6"/><rect x="18" y="32" width="6" height="6"/><rect x="18" y="44" width="6" height="6"/><path d="M28 23h14M28 35h14M28 47h14"/></svg>
  <p>Choose the Plan<br>You Like Best</p></div>
<div class="step green" style="left:853px"><span class="n">4</span>
  <svg width="60" height="64" viewBox="0 0 60 64" fill="none" stroke="#fff" stroke-width="2.5"><rect x="6" y="10" width="48" height="32" rx="3"/><path d="M22 60V30a4 4 0 018 0v12l10 2v16"/></svg>
  <p>Place Your Order and<br>Activate Your Plan</p></div>

<!-- Bring your phone -->
<section class="byop abs">
  <div class="byop-art" role="img" aria-label="White marble-finish smartphone lying at an angle"></div>
  <h2><b>Love your current phone?<br>Bring it to Telvora</b><br>and enjoy seamless<br>connectivity.<span class="dash"></span></h2>
</section>
<a class="btn" style="left:557px;top:2542px;width:218px;height:47px;background:var(--green);font-size:14px">Check Compatibility</a>
<a class="btn" style="left:794px;top:2542px;width:128px;height:47px;background:var(--black);font-size:14px">Shop Now</a>

<!-- Testimonials -->
<div class="abs" style="left:0;width:1200px;top:2739px"><h2 class="heading"><b>What Our</b> Client Says</h2><div class="heading-rule"></div></div>
<div class="review" style="left:109px"><p>I've been using Veradilo for a few months now, and I must say its connection is excellent. Whether I'm in the United States or visiting family</p><div class="avatar"></div><div class="who">Marisol Pendra</div><div class="stars">★★★★★</div><div class="quote">”</div></div>
<div class="review" style="left:444px"><p>I've been using Veradilo for a few months now, and I must say its connection is excellent. Whether I'm in the United States or visiting family</p><div class="avatar"></div><div class="who">Marisol Pendra</div><div class="stars">★★★★★</div><div class="quote">”</div></div>
<div class="review" style="left:778px"><p>I've been using Veradilo for a few months now, and I must say its connection is excellent. Whether I'm in the United States or visiting family</p><div class="avatar"></div><div class="who">Marisol Pendra</div><div class="stars">★★★★★</div><div class="quote">”</div></div>

<!-- FAQ -->
<div class="faq-bg abs"></div>
<div class="abs" style="left:0;width:1200px;top:3182px"><h2 class="heading"><b>Frequently Asked</b> Questions</h2><div class="heading-rule"></div></div>
<div class="faq" style="top:3296px;height:53px"><span class="q">When will my auto-renewal payment be deducted?</span><span class="chev"></span></div>
<div class="faq" style="top:3367px;height:53px"><span class="q">Can I download content such as ringtones, games, graphics?</span><span class="chev"></span></div>
<div class="faq" style="top:3437px;height:53px"><span class="q">I purchased additional data, minutes, or text messages. Do they accumulate if not used?</span><span class="chev"></span></div>
<div class="faq" style="top:3510px;height:53px"><span class="q">I ported my number - what is my Veradilo password?</span><span class="chev"></span></div>
<div class="faq" style="top:3580px;height:101px"><span class="q">Can I choose my Veradilo phone number?</span><span class="chev"></span><span class="a">Numbers are randomly assigned, based on the zip code you enter when activating your phone or SIM card.</span></div>

<!-- Footer -->
<footer class="footer abs"></footer>
<div class="foot-brand abs"><div class="mark"></div><div class="name">telvora</div></div>
<div class="foot">
  <h4 style="left:472px;top:3827px">Links</h4>
  <ul class="foot-links"><li>Home</li><li>Plans</li><li>Bring Your Own phone</li><li>Activate &nbsp;Coverage</li><li>SupportAccount</li><li>Account</li></ul>
  <h4 style="left:713px;top:3827px">Subscribe for Updates</h4>
</div>
<div class="email abs"><span>Email Address</span></div>
<a class="btn" style="left:969px;top:3875px;width:120px;height:44px;background:var(--green)">Submit</a>
<div class="abs" style="left:713px;top:3946px;color:var(--white);font:500 13px Roboto,sans-serif">&#9745; &nbsp;Yes, Please Contact me.</div>
<span class="social" style="left:713px" aria-label="Social link"></span>
<span class="social" style="left:756px" aria-label="Social link"></span>
<span class="social" style="left:798px" aria-label="Social link"></span>
<div class="abs" style="left:111px;top:4052px;width:978px;height:1px;background:#333"></div>
<div class="copy abs">© 2025 &nbsp;Telvora &nbsp;| &nbsp;All Rights Reserved</div>

</body>
</html>
```